Namibia currently imports 60% of its food. Harvest Crest Oruva is an initiative which will assist Namibia to become self sustainable in terms of food production. We aim to do this through the development of 3 agricultural production zones which will include farming zones, local farmer assistance, processing and distribution of the final products. Please see our project overview attached.

```html
<!DOCTYPE html>
<html lang="en">
<head>
<meta charset="utf-8">
<title>Harvest Crest Oruva</title>
<link href="https://fonts.googleapis.com/css2?family=Cinzel:wght@400;600;700&family=Barlow:wght@400;500;600;700&display=swap" rel="stylesheet">
<style>
:root{
  --green:#0b6b35;
  --green-dark:#07532a;
  --tan:#c4a27e;
  --cream:#f9f1ea;
  --ink:#1d1d1d;
  --body:#555;
  --white:#fff;
  --footer:#050505;
  --footer-bar:#1e1e1e;
}
*{box-sizing:border-box;margin:0;padding:0}
html,body{width:1200px;height:4234px;overflow:hidden}
body{position:relative;font-family:"Barlow",Arial,sans-serif;color:var(--ink);background:var(--white)}
.abs{position:absolute}
.serif{font-family:"Cinzel",Georgia,serif}
.btn{position:absolute;background:var(--green);color:var(--white);border-radius:22px;font-weight:700;font-size:13px;display:flex;align-items:center;justify-content:center;gap:5px;text-transform:uppercase}
.btn .dot{width:11px;height:11px;border-radius:50%;background:var(--white);color:var(--green);font-size:9px;display:flex;align-items:center;justify-content:center}

/* hero */
.hero{position:absolute;left:0;top:0;width:1200px;height:667px;background:linear-gradient(180deg,#dcd8d2 0%,#cfd2c8 22%,#7f9a3a 38%,#55802a 60%,#3f6a1e 80%,#a98b47 100%)}
.brand{position:absolute;left:145px;top:32px;font-family:"Cinzel",Georgia,serif;font-size:26px;color:var(--green);font-weight:600;letter-spacing:.5px}
.nav{position:absolute;left:524px;top:38px;display:flex;gap:30px;font-size:13px;color:#333}
.nav .active{color:var(--green);border-bottom:2px solid var(--green);padding-bottom:6px}
.hero-title{position:absolute;left:0;width:1200px;top:322px;text-align:center;font-family:"Cinzel",Georgia,serif;font-size:76px;line-height:80px;color:var(--white);font-weight:400}
.hero-dot{position:absolute;top:565px;width:46px;height:46px;border-radius:50%;background:rgba(255,255,255,.35);color:var(--white);display:flex;align-items:center;justify-content:center;font-size:16px}

/* education */
.education{position:absolute;left:0;top:667px;width:1200px;height:522px;background:var(--green)}
.section-title{position:absolute;left:0;width:1200px;text-align:center;font-family:"Cinzel",Georgia,serif;font-weight:600}
.section-title .accent{color:var(--tan)}
.edu-item{position:absolute;top:183px;width:200px;text-align:center;color:var(--white);font-size:19px;line-height:25px}
.edu-ring{width:158px;height:158px;border:2px solid var(--tan);border-radius:50%;margin:0 auto 14px;display:flex;align-items:center;justify-content:center}
.edu-icon{width:74px;height:74px;border-radius:50%;background:rgba(196,162,126,.25)}
.edu-arrow{position:absolute;top:272px;color:var(--tan);font-size:22px}

/* feature cards */
.panel{position:absolute;background:var(--cream);border-radius:12px}
.photo{position:absolute;border-radius:12px}
.card-title{font-family:"Cinzel",Georgia,serif;font-size:35px;font-weight:600;line-height:44px;color:var(--ink)}
.card-text{font-size:13px;line-height:21.5px;color:var(--body);text-align:justify}

/* empowerment */
.empower{position:absolute;left:0;top:2502px;width:1200px;height:684px;background:var(--green)}
.empower-intro{position:absolute;left:200px;width:800px;top:152px;text-align:center;color:var(--white);font-size:13px;line-height:22px}
.area{position:absolute;width:440px;height:97px;background:var(--white);border-radius:4px;display:flex;align-items:center}
.area-num{width:77px;height:77px;margin:0 20px 0 10px;background:var(--tan);border-radius:4px;color:var(--white);font-size:19px;display:flex;align-items:center;justify-content:center;flex:none}
.area-text{font-size:15px;line-height:25px;color:#555;padding-right:20px}

/* sustainability */
.sub-head{font-size:19px;font-weight:700;color:var(--tan)}
.yield{display:flex;align-items:center;gap:14px;font-size:12.5px;color:#555;line-height:24px}
.tick{width:11px;height:11px;border-radius:50%;background:var(--green);display:inline-block}

/* footer */
.footer{position:absolute;left:0;top:3835px;width:1200px;height:310px;background:var(--footer);color:var(--white)}
.footer h4{font-size:22px;font-weight:700;color:var(--tan)}
.footer ul{list-style:none;font-size:13px;line-height:24px;margin-top:16px}
.footer li::before{content:"»";color:var(--white);margin-right:16px}
.contact-row{display:flex;gap:16px;font-size:13px;line-height:24px}
.contact-row .ic{color:var(--tan);width:12px}
.footer-bar{position:absolute;left:0;top:4145px;width:1200px;height:89px;background:var(--footer-bar);color:var(--white);font-size:13px;text-align:center;padding-top:38px}
</style>
</head>
<body>

<header class="hero" role="img" aria-label="Photo of green crop rows with a tractor spraying the field">
  <div class="brand">Harvest Crest Oruva</div>
  <nav class="nav"><span class="active">Home</span><span>About Us</span><span>Services</span><span>Blog</span><span>Contact</span></nav>
  <div class="btn" style="left:922px;top:26px;width:132px;height:41px;font-size:13px">Get in touch</div>
  <h1 class="hero-title">Harvest Crest<br>Oruva</h1>
  <div class="hero-dot" style="left:549px">‹</div>
  <div class="hero-dot" style="left:605px">›</div>
</header>

<section class="education">
  <h2 class="section-title" style="top:100px;font-size:38px;color:var(--white)"><span class="accent">“Harvest Crest”</span> Education</h2>
  <span class="edu-arrow" style="left:62px">◀</span>
  <span class="edu-arrow" style="left:1116px">▶</span>
  <div class="edu-item" style="left:120px"><div class="edu-ring"><div class="edu-icon" role="img" aria-label="Gear with plant icon"></div></div>Farm<br>Management</div>
  <div class="edu-item" style="left:309px"><div class="edu-ring"><div class="edu-icon" role="img" aria-label="Hand holding seedling icon"></div></div>Crop<br>Management</div>
  <div class="edu-item" style="left:498px"><div class="edu-ring"><div class="edu-icon" role="img" aria-label="Field with water drop icon"></div></div>Soil Health and<br>Irrigation</div>
  <div class="edu-item" style="left:689px"><div class="edu-ring"><div class="edu-icon" role="img" aria-label="Team with gear icon"></div></div>Business<br>Management</div>
  <div class="edu-item" style="left:878px"><div class="edu-ring"><div class="edu-icon" role="img" aria-label="Chart on screen icon"></div></div>Marketing</div>
</section>

<div class="panel" style="left:544px;top:1356px;width:528px;height:398px"></div>
<div class="photo" role="img" aria-label="Photo of a farm worker harvesting potatoes into crates beside a tractor" style="left:128px;top:1309px;width:416px;height:490px;background:linear-gradient(180deg,#7d93b8 0%,#a8b4c4 35%,#2f55a8 55%,#7a5a4e 80%,#8a5a52 100%)"></div>
<div class="abs" style="left:579px;top:1392px;width:456px">
  <h2 class="card-title">Namibia Needs Food</h2>
  <p class="card-text" style="margin-top:18px">Namibia is a young democracy in Sub-Saharan Africa with a population of approximately 2.5 Million people. The country’s agricultural sector has been slow to keep up with the increasing population. As a consequence, approximately 60% of the food required to feed the nation is imported. The elevated cost of these imported foods means a large proportion of the population consume food with low nutritional value. Despite vast tracts of available arable land and abundant water resources (both above and below ground), the agricultural sector has struggled to capitalise. This is largely due to a lack of investment, technical knowledge and available technologies.</p>
</div>
<div class="btn" style="left:579px;top:1668px;width:147px;height:40px">Learn more <span class="dot">›</span></div>

<div class="panel" style="left:128px;top:1927px;width:528px;height:398px"></div>
<div class="photo" role="img" aria-label="Photo of fresh potatoes in front of a green potato field" style="left:656px;top:1881px;width:416px;height:490px;background:linear-gradient(180deg,#3c7a2a 0%,#4f8f35 45%,#6b5a3e 65%,#c9b48e 85%,#8d7552 100%)"></div>
<div class="abs" style="left:166px;top:1954px;width:458px">
  <h2 class="card-title"><span style="color:var(--tan)">“Harvest Crest”</span><br>Solution</h2>
  <p class="card-text" style="margin-top:18px">The long term intention of the Harvest Crest Oruva program would be to establish 3 distinct food production and processing zones which have access to large amounts of arable land, with high quality soil and strong water resources, as well as good transport connections to relevant markets.</p>
  <p class="card-text" style="margin-top:18px;text-align:left">Otavi Region - Central Namibia<br>Kavango Region - North Namibia<br>Neckartal Dam - South Namibia</p>
</div>
<div class="btn" style="left:166px;top:2248px;width:147px;height:40px">Learn more <span class="dot">›</span></div>

<section class="empower">
  <h2 class="section-title" style="top:92px;font-size:36px;color:var(--white)">Empowerment Production Areas</h2>
  <p class="empower-intro">Namibia has a substantial amount of unutilised arable land in possession of either the government, or private individuals who do not have the resources or skills to develop the land into a viable food production asset. Harvest Crest Oruva aims to empower these organisations and individuals by assisting them to develop the land and operate them successfully. Support will come in the form of:</p>
  <div class="area" style="left:145px;top:238px"><div class="area-num">01</div><div class="area-text">Provision of pivots and mobile drip irrigation on a lease to own basis</div></div>
  <div class="area" style="left:615px;top:238px"><div class="area-num">04</div><div class="area-text">Planting and harvesting services</div></div>
  <div class="area" style="left:145px;top:350px"><div class="area-num">02</div><div class="area-text">Rental of tractors and impliments required</div></div>
  <div class="area" style="left:615px;top:350px"><div class="area-num">05</div><div class="area-text">Full agronomy services and insurance</div></div>
  <div class="area" style="left:145px;top:462px"><div class="area-num">03</div><div class="area-text">Chemical and fertiliser supply</div></div>
  <div class="area" style="left:615px;top:462px"><div class="area-num">06</div><div class="area-text">Guaranteed purchase of all crops at market prices</div></div>
</section>

<div class="abs" style="left:132px;top:3287px;width:440px;height:440px;border-radius:50%;background:var(--tan)"></div>
<div class="abs" role="img" aria-label="Photo of solar panels beside a green wheat field under a cloudy sky" style="left:144px;top:3299px;width:416px;height:416px;border-radius:50%;background:linear-gradient(180deg,#5b8fd0 0%,#cdd9e6 30%,#2f5a2a 45%,#3b4f6e 55%,#8fb04a 70%,#9cbc56 100%)"></div>
<div class="abs" style="left:600px;top:3290px;width:460px">
  <h2 class="card-title" style="font-size:36px">Sustainability</h2>
  <div class="sub-head" style="margin-top:6px">Processing Facilities</div>
  <p class="card-text" style="margin-top:10px">Each of the allocated production zones will be furnished with handling, processing and milling facilities for all crops produced as part of the program. These will include Potatoes, Maize and Wheat.</p>
  <p class="card-text" style="margin-top:18px;text-align:left">Harvest Crest Oruva will undertake primary production of the food goods and market them into the Namibian food supply chain.</p>
  <div class="sub-head" style="margin-top:18px">Anticipated yields per production zone:</div>
  <div style="margin-top:10px">
    <div class="yield"><span class="tick"></span>Potatoes - 20,000 Ton Per Annum</div>
    <div class="yield"><span class="tick"></span>Maize - 16,000 Ton Per Annum</div>
    <div class="yield"><span class="tick"></span>Wheat - 6,000 Ton Per Annum</div>
  </div>
</div>
<div class="btn" style="left:601px;top:3664px;width:147px;height:40px">Learn more <span class="dot">›</span></div>

<footer class="footer">
  <div class="abs" style="left:200px;top:90px;width:290px;text-align:center;font-family:'Barlow',Arial,sans-serif;font-size:32px;font-weight:700;color:var(--green)">Harvest Crest Oruva</div>
  <div class="abs" style="left:575px;top:100px">
    <h4>Quick Links</h4>
    <ul><li>Home</li><li>About Us</li><li>Services</li><li>Blog</li><li>Contact</li></ul>
  </div>
  <div class="abs" style="left:791px;top:100px;width:220px">
    <h4>Contact Us</h4>
    <div style="margin-top:16px">
      <div class="contact-row"><span class="ic">●</span><span>123, Lorem ipsum dolor sit<br>consectetur</span></div>
      <div class="contact-row" style="margin-top:24px"><span class="ic">✆</span><span>+1888 888 8888</span></div>
      <div class="contact-row"><span class="ic">✉</span><span>hello@harvestcrestoruva.org</span></div>
    </div>
  </div>
</footer>
<div class="footer-bar">© Copyrights 2024 | All Rights Reserved</div>

</body>
</html>
```